Kestrel Facilities Business Card Design

We would now like to design business cards with the new Kestrel Facilities logo

Target Market(s)

Professional

Industry/Entity Type

Professional services

Contact Information for Business Card

Employee name, title, phone number, email address, corporate office address and logo.

Font styles to use
Sans Serif

Colors
0054AA
0677BA
7BADD7
CADEEF
E8F1F8

Requirements
Must have
• My logo
Should not have
• any other pictures or images besides my logo

```html
<!DOCTYPE html>
<html lang="en">
<head>
<meta charset="utf-8">
<title>Kestrel Facilities Business Card</title>
<link rel="stylesheet" href="https://fonts.googleapis.com/css2?family=Roboto:wght@400;500;700&display=swap">
<style>
  :root {
    --stage: #d6d6d8;
    --card-white: #ffffff;
    --brand-blue: #0080e6;
    --ink-grey: #3a3a3c;
    --accent-grey: #8a8a8c;
    --back-black: #141414;
    --back-sheen: #2a2a2c;
    --name-white: #ffffff;
  }
  * { box-sizing: border-box; margin: 0; padding: 0; }
  html, body { width: 1200px; height: 800px; overflow: hidden; }
  body {
    background: var(--stage);
    font-family: "Roboto", Arial, sans-serif;
    position: relative;
  }
  .card {
    position: absolute;
    left: 320px;
    width: 560px;
    height: 320px;
    box-shadow: 0 8px 24px rgba(0,0,0,0.18);
    overflow: hidden;
  }
  .card-front { top: 50px; background: var(--card-white); }
  .card-back { top: 430px; background: var(--back-black); }

  .brand {
    position: absolute;
    left: 48px;
    top: 78px;
    display: flex;
    align-items: center;
    gap: 12px;
  }
  .brand-square {
    width: 34px;
    height: 34px;
    background: var(--brand-blue);
  }
  .brand-name {
    color: var(--brand-blue);
    font-weight: 700;
    font-size: 26px;
    line-height: 1.05;
    letter-spacing: 0.5px;
    text-transform: uppercase;
  }

  .contact {
    position: absolute;
    left: 50px;
    top: 170px;
    list-style: none;
    color: var(--ink-grey);
    font-size: 13px;
    line-height: 1.35;
  }
  .contact li { display: flex; align-items: flex-start; gap: 9px; margin-bottom: 5px; }
  .contact svg { width: 12px; height: 12px; margin-top: 2px; flex: none; fill: var(--brand-blue); }

  .name-band {
    position: absolute;
    right: 0;
    top: 72px;
    width: 255px;
    height: 88px;
    background: var(--brand-blue);
    color: var(--name-white);
    padding: 22px 0 0 30px;
  }
  .person-name {
    font-weight: 700;
    font-size: 22px;
    letter-spacing: 0.5px;
    text-transform: uppercase;
  }
  .person-title { font-size: 14px; margin-top: 2px; }

  .edge-mark {
    position: absolute;
    left: 0;
    bottom: 0;
    width: 70px;
    height: 14px;
    background: var(--accent-grey);
  }

  .back-texture {
    position: absolute;
    inset: 0;
    background: linear-gradient(120deg, var(--back-sheen) 0%, var(--back-black) 55%);
  }
  .back-brand {
    position: absolute;
    right: 48px;
    bottom: 44px;
    color: var(--brand-blue);
    font-weight: 700;
    font-size: 12px;
    letter-spacing: 0.5px;
    text-transform: uppercase;
  }
</style>
</head>
<body>
  <section class="card card-front" aria-label="Business card front">
    <div class="brand">
      <span class="brand-square"></span>
      <span class="brand-name">Kestrel<br>Facilities</span>
    </div>

    <ul class="contact">
      <li>
        <svg viewBox="0 0 12 12" aria-hidden="true"><path d="M6 0a4 4 0 0 0-4 4c0 3 4 8 4 8s4-5 4-8a4 4 0 0 0-4-4zm0 5.5A1.5 1.5 0 1 1 6 2.5a1.5 1.5 0 0 1 0 3z"/></svg>
        <span>2214 Birchwood Lane<br>Anchorage, Alaska 99517</span>
      </li>
      <li>
        <svg viewBox="0 0 12 12" aria-hidden="true"><path d="M2.5 0.5l2 2-1 1.5c.8 1.6 2 2.8 3.5 3.5l1.5-1 2 2-1.5 2C4.5 10.5 1.5 7.5.5 2z"/></svg>
        <span>369-555-0142</span>
      </li>
      <li>
        <svg viewBox="0 0 12 12" aria-hidden="true"><path d="M0 2h12v8H0zm1 1v.4l5 3.2 5-3.2V3z"/></svg>
        <span>info@kestrelfacilities.com</span>
      </li>
      <li>
        <svg viewBox="0 0 12 12" aria-hidden="true"><circle cx="6" cy="6" r="5.5"/></svg>
        <span>kestrelfacilities.com</span>
      </li>
    </ul>

    <div class="name-band">
      <p class="person-name">Daniel Reyes</p>
      <p class="person-title">President</p>
    </div>

    <span class="edge-mark"></span>
  </section>

  <section class="card card-back" aria-label="Business card back">
    <div class="back-texture" role="img" aria-label="Tone-on-tone repeating brand pattern on black"></div>
    <span class="back-brand">Kestrel Facilities</span>
  </section>
</body>
</html>
```